New Business Card Design Project

I need a design for business cards, i am an electrical business called "Corvane Electrical and Communications" i need the cards to be double sided with the company logo on the back (attached) the front needs to say my company name, web site, email address, telephone number, and ABN number and electrical license number. I am open to different arrangements of the information but would like the background to be incorporating something electrical or something that looks smart. open to all additional ideas also.

The company colours are orange and grey see logo attached.

Business Name: Corvane Electrical and Communications
Website: corvaneelectricalandcomms.example.com.au
Email: brent@corvaneelectricalandcomms.example.com.au
Telephone(mobile): 0481209736
ABN: 71208349162
Lic No: 418273D

Target Market(s)

Business entities, Project Managers, Accounts, Clients

Industry/Entity Type

Electrician

Contact Information for Business Card

I need a design for business cards, i am an electrical business called "Corvane Electrical and Communications" i need the cards to be double sided with the company logo on the back (attached) the front needs to say my company name

Font styles to use
Serif
Sans Serif

Colors
f37122
5c5c5c

Requirements
Must have
• Must have the Logo on the back open to different ways of it being on the back but had in mind to keep it central but again open to other options
Nice to have
• A real modern cool background that is eye catching yet contemporary
Should not have
• No backgrounds of a light bulb or plug or anything like that

```html
<!DOCTYPE html>
<html lang="en">
<head>
<meta charset="utf-8">
<title>Corvane Electrical and Communications – Business Cards</title>
<link href="https://fonts.googleapis.com/css2?family=Questrial&display=swap" rel="stylesheet">
<style>
  :root {
    --orange: #f37122;
    --amber: #f5a623;
    --grey: #5c5c5c;
    --card-grey: #5a5a5a;
    --stage: #2e2e2e;
    --navy-deep: #05061a;
    --navy: #0e1a5c;
    --electric: #2f6cf0;
    --white: #ffffff;
    --ink: #3a3a3a;
  }
  * { box-sizing: border-box; margin: 0; padding: 0; }
  html, body {
    width: 1200px; height: 900px; overflow: hidden;
    background: var(--stage);
    font-family: "Questrial", "Century Gothic", sans-serif;
  }
  .canvas { position: relative; width: 1200px; height: 900px; }

  .card {
    position: absolute;
    width: 620px; height: 345px;
    border-radius: 22px;
    overflow: hidden;
  }

  /* Back of card */
  .card-back { left: 150px; top: 70px; background: var(--card-grey); }
  .brand {
    position: absolute; left: 0; right: 0; top: 0; height: 260px;
    display: flex; align-items: center; justify-content: center; gap: 18px;
  }
  .brand-mark {
    width: 30px; height: 30px; border-radius: 50%;
    background: var(--amber); flex: none;
  }
  .brand-name {
    color: var(--white); font-size: 34px; line-height: 1.2;
    letter-spacing: 1px; text-transform: uppercase; text-align: center;
  }
  .brand-name small { display: block; font-size: 17px; letter-spacing: 1.5px; }
  .back-web {
    position: absolute; left: 0; right: 0; bottom: 40px;
    text-align: center; color: var(--white); font-size: 16px;
  }
  .back-web .domain { color: var(--amber); }

  /* Front of card */
  .card-front { left: 430px; top: 470px; background: var(--navy-deep); }
  .energy-field {
    position: absolute; left: 0; top: 0; width: 620px; height: 238px;
    background: radial-gradient(ellipse at 62% 40%, var(--electric) 0%, var(--navy) 45%, var(--navy-deep) 100%);
  }
  .base-band {
    position: absolute; left: 0; right: 0; top: 238px; bottom: 0;
    background: var(--white); border-top: 4px solid var(--amber);
  }
  .front-brand {
    position: absolute; left: 28px; top: 0; height: 238px; width: 236px;
    display: flex; align-items: center; gap: 10px;
  }
  .front-brand .brand-mark { width: 16px; height: 16px; }
  .front-brand .brand-name { font-size: 24px; text-align: left; }
  .front-brand .brand-name small { font-size: 11px; letter-spacing: 0.5px; }
  .divider {
    position: absolute; left: 268px; top: 62px;
    width: 1px; height: 110px; background: var(--amber);
  }
  .contact { position: absolute; left: 282px; top: 56px; color: var(--white); }
  .contact-name {
    color: var(--amber); font-size: 24px; text-transform: uppercase; letter-spacing: 0.5px;
  }
  .contact-role { font-size: 12px; text-transform: uppercase; margin-bottom: 10px; }
  .contact-line {
    display: flex; align-items: center; gap: 7px;
    font-size: 11.5px; line-height: 18px;
  }
  .contact-line svg { width: 10px; height: 10px; flex: none; }
  .licence, .abn {
    position: absolute; font-size: 14px; color: var(--ink);
  }
  .licence { left: 34px; bottom: 26px; }
  .abn { right: 30px; bottom: 26px; }
  .label { color: var(--amber); }
</style>
</head>
<body>
<main class="canvas">

  <section class="card card-back" aria-label="Business card back">
    <div class="brand">
      <span class="brand-mark"></span>
      <p class="brand-name">Corvane<small>Electrical &amp; Communications</small></p>
    </div>
    <p class="back-web">www.<span class="domain">corvaneelectricalandcomms</span>.example.com.au</p>
  </section>

  <section class="card card-front" aria-label="Business card front">
    <div class="energy-field" role="img" aria-label="Glowing blue streaks of electric light on a dark background"></div>
    <div class="base-band"></div>

    <div class="front-brand">
      <span class="brand-mark"></span>
      <p class="brand-name">Corvane<small>Electrical &amp; Communications</small></p>
    </div>
    <div class="divider"></div>
    <div class="contact">
      <p class="contact-name">Marlo Fenwick</p>
      <p class="contact-role">Director</p>
      <p class="contact-line">
        <svg viewBox="0 0 10 10"><path d="M2 1 L4 3 L3 4 Q4 6 6 7 L7 6 L9 8 L8 9 Q4 9 1 5 Q1 2 2 1Z" fill="var(--amber)"/></svg>
        0481 209 736
      </p>
      <p class="contact-line">
        <svg viewBox="0 0 10 10"><rect x="0.7" y="2" width="8.6" height="6" fill="none" stroke="var(--amber)" stroke-width="1.2"/><path d="M1 2.5 L5 5.5 L9 2.5" fill="none" stroke="var(--amber)" stroke-width="1.2"/></svg>
        brent@corvaneelectricalandcomms.example.com.au
      </p>
      <p class="contact-line">
        <svg viewBox="0 0 10 10"><circle cx="5" cy="5" r="4.2" fill="none" stroke="var(--amber)" stroke-width="1.2"/><path d="M1 5 H9 M5 1 Q2.5 5 5 9 M5 1 Q7.5 5 5 9" fill="none" stroke="var(--amber)" stroke-width="0.9"/></svg>
        www.corvaneelectricalandcomms.example.com.au
      </p>
    </div>
    <p class="abn"><span class="label">ABN:</span> 71208349162</p>
    <p class="licence"><span class="label">Lic No:</span> 418273D</p>
  </section>

</main>
</body>
</html>
```